Brochure 2 fold and Trifold

We need 2 types of brochure (2 fold and Trifold) design for our Brand "VELVET DAWN" Logo (La douceur de Mirelle) is in rose gold color
Target Market(s)
Women ages 17 and up
Industry/Entity Type
Supplement
Font styles to use
Serif
Script
Requirements
Must have
- Rose gold color tone make it look premium, minimalist look

```html
<!DOCTYPE html>
<html lang="en">
<head>
<meta charset="utf-8">
<title>Velvet Dawn – Skin Whitening &amp; Sun Protection</title>
<link href="https://fonts.googleapis.com/css2?family=Allura&family=Poppins:wght@600;700&family=Didact+Gothic&display=swap" rel="stylesheet">
<style>
:root{
  --rose:#f2c5b6;
  --rose-deep:#e3a794;
  --rose-soft:#f5d3c7;
  --ink:#3c3c3c;
  --muted:#888;
  --white:#fff;
}
*{margin:0;padding:0;box-sizing:border-box}
html,body{width:1200px;height:840px;overflow:hidden;background:var(--white)}
.brochure{position:relative;width:1200px;height:840px;overflow:hidden;font-family:"Didact Gothic",sans-serif;color:var(--ink)}

/* left panel */
.ingredients{position:absolute;left:0;top:0;width:410px;height:840px;background:var(--rose);color:var(--white);padding:0 22px;z-index:2}
.title-script{font-family:"Allura",cursive;font-size:80px;line-height:1;position:absolute;left:16px;top:56px;width:380px;font-weight:400;white-space:nowrap;letter-spacing:-.5px}
.title-sub{font-family:"Poppins",sans-serif;font-weight:700;font-size:34px;position:absolute;left:24px;top:130px;letter-spacing:.5px;white-space:nowrap}
.ingredient{position:absolute;left:24px;width:362px}
.ingredient h3{display:inline-block;background:var(--white);color:var(--rose-deep);font-family:"Poppins",sans-serif;font-weight:600;font-size:16px;padding:1px 8px 0 2px;margin-bottom:6px}
.ingredient p{font-size:17px;line-height:1.2;text-align:justify;letter-spacing:.2px}
.i1{top:228px}.i2{top:440px}.i3{top:648px}

/* centre */
.portrait{position:absolute;left:410px;top:0;width:390px;height:840px;background:linear-gradient(100deg,#e9e9e9 0%,#f7f7f7 45%,#fdfdfd 100%)}
.frame{position:absolute;left:426px;top:21px;width:358px;height:795px;border:1.5px solid var(--rose-soft)}
.benefits-title{position:absolute;left:462px;top:468px;font-family:"Allura",cursive;font-size:84px;color:var(--rose-deep);line-height:1}
.benefits-sub{position:absolute;left:462px;top:540px;color:var(--rose-deep);font-size:28px;white-space:nowrap}
.benefits-sub strong{font-family:"Poppins",sans-serif;font-weight:600;font-size:25px}
.benefits{position:absolute;left:459px;top:586px;width:282px;height:236px;background:var(--rose);list-style:none;padding:12px 10px 0 14px;color:var(--white);font-size:16px;line-height:1.1}
.benefits li{position:relative;padding-left:22px;margin-bottom:13px}
.benefits li::before{content:"";position:absolute;left:0;top:3px;width:11px;height:11px;border-radius:50%;background:var(--white)}

/* right */
.divider{position:absolute;left:800px;top:0;height:840px;border-left:1.5px dashed #cfcfcf}
.studies-head{position:absolute;left:868px;top:11px;width:261px;height:46px;background:var(--rose);color:var(--white);font-family:"Poppins",sans-serif;font-weight:600;font-size:27px;text-align:center;line-height:48px}
.chart{position:absolute}
.chart-main{left:820px;top:78px}
.chart-melasma{left:880px;top:494px}
.study-note{position:absolute;left:837px;width:335px;font-size:16px;line-height:1.22}
.study-note cite{display:block;margin-top:10px;font-size:14.5px;color:var(--muted);font-style:italic}
.n1{top:352px}.n2{top:682px}
</style>
</head>
<body>
<main class="brochure">

  <section class="ingredients">
    <h1 class="title-script">skin whitening</h1>
    <h2 class="title-sub">&amp;SUN PROTECTION</h2>

    <article class="ingredient i1">
      <h3>1.PhytoBloom</h3>
      <p>An award winning natural supplement using non-GMO tomato species rich in colourless carotenoids, phytoene and phytofluene. This patented combination provides superior whitening, UVA and UVB protection, anti-inflammatory and antioxidant properties.</p>
    </article>
    <article class="ingredient i2">
      <h3>2.Polypodium leucotomos</h3>
      <p>Naturally extracted from a tropical natural fern found in the Americas, it has been used for centuries by the natives for its superior benefits. Now clinically proven to protect against UV radiation due to its antioxidant, anti-inflammatory and DNA repair abilities.</p>
    </article>
    <article class="ingredient i3">
      <h3>3.L-Cysteine</h3>
      <p>A potent amino acid that has very high skin-whitening abilities. It prevents the production of pigment cells when the skin is exposed to UV rays and stimulates the production of Glutathione, another strong skin-whitening antioxidant.</p>
    </article>
  </section>

  <div class="portrait" role="img" aria-label="Soft black and white close-up portrait photograph of a woman's eye and lips"></div>
  <div class="frame"></div>
  <div class="benefits-title">Benefits</div>
  <div class="benefits-sub">of <strong>VELVET DAWN</strong></div>
  <ul class="benefits">
    <li>Skin Whitening</li>
    <li>Collagen Protection</li>
    <li>DNA Repair</li>
    <li>Prevents Against<br>Premature Skin Aging</li>
    <li>Enhanced Antioxidant<br>&amp; Anti-inflammatory effects</li>
    <li>Natural UV Protection effects</li>
  </ul>

  <div class="divider"></div>

  <section class="studies">
    <div class="studies-head">CLINICAL STUDIES</div>

    <svg class="chart chart-main" width="360" height="262" viewBox="0 0 360 262" font-family="Didact Gothic, sans-serif">
      <text x="180" y="14" font-size="9.5" font-weight="700" text-anchor="middle" fill="#333">Average clinical improvement of skin parameters</text>
      <g font-size="7.5" fill="#666" text-anchor="end">
        <text x="20" y="196">0</text><text x="20" y="180">10</text><text x="20" y="164">20</text><text x="20" y="147">30</text><text x="20" y="131">40</text><text x="20" y="115">50</text><text x="20" y="99">60</text><text x="20" y="83">70</text><text x="20" y="66">80</text><text x="20" y="50">90</text><text x="20" y="34">100</text>
      </g>
      <line x1="26" y1="193" x2="355" y2="193" stroke="#ccc"/>
      <g fill="#e3a794">
        <rect x="40" y="102" width="16" height="91"/>
        <rect x="105" y="88" width="16" height="105"/>
        <rect x="170" y="94" width="16" height="99"/>
        <rect x="235" y="151" width="16" height="42"/>
        <rect x="300" y="146" width="16" height="47"/>
      </g>
      <g fill="#f5cdbf">
        <rect x="58" y="78" width="16" height="115"/>
        <rect x="123" y="68" width="16" height="125"/>
        <rect x="188" y="44" width="16" height="149"/>
        <rect x="253" y="114" width="16" height="79"/>
        <rect x="318" y="94" width="16" height="99"/>
      </g>
      <g font-size="7.5" fill="#444" text-anchor="middle">
        <text x="57" y="208">Dryness</text><text x="122" y="208">Roughness</text><text x="187" y="208">Suppleness</text><text x="252" y="208">Complexion evenness</text><text x="317" y="208">Texture</text>
      </g>
      <g font-size="6.5" fill="#888">
        <rect x="155" y="220" width="5" height="5" fill="#e3a794"/><text x="163" y="225">Day 42</text>
        <rect x="190" y="220" width="5" height="5" fill="#f5cdbf"/><text x="198" y="225">Day 84</text>
      </g>
      <text x="180" y="246" font-size="7" fill="#555" text-anchor="middle"><tspan font-weight="700">Figure 2.</tspan> Graphic representation of the average changes in clinical scoring.</text>
    </svg>

    <p class="study-note n1">Skin improvement results of a clinical study conducted by dermatologists measuring skin quality after 12 weeks use of colourless carotenoids.
      <cite>(Global Skin Review 2015: 2(4) Page178-182)</cite></p>

    <svg class="chart chart-melasma" width="220" height="170" viewBox="0 0 220 170" font-family="Didact Gothic, sans-serif">
      <g font-size="12" fill="#444" text-anchor="middle">
        <text x="11" y="38">6</text><text x="11" y="80">4</text><text x="11" y="122">2</text><text x="11" y="164">0</text>
      </g>
      <line x1="28" y1="160" x2="162" y2="160" stroke="#bbb"/>
      <rect x="56" y="40" width="37" height="120" fill="#e3a794"/>
      <rect x="96" y="90" width="36" height="70" fill="#f5cdbf"/>
      <path d="M70 30 Q98 0 122 28" fill="none" stroke="#999" stroke-width="4"/>
      <path d="M114 24 L126 38 L130 20 Z" fill="#999"/>
      <text x="132" y="18" font-size="13" font-weight="700" fill="#333">-42,1%</text>
      <text x="136" y="30" font-size="9" fill="#888">p &lt; 0,05</text>
    </svg>

    <p class="study-note n2">Reduction in intensity of melasma with usage of daily oral Polypodium Leucotomos for 12 weeks with sunscreen SPF 45.
      <cite>(Journal of Clinical Skin Science 2012: 66(4) Page AB21).</cite></p>
  </section>

</main>
</body>
</html>
```